Redesign of the UI of a customer service platform

To improve the user experience of our customers, we need a new design for our agent interface of our customer service platform (velorant.com).
The focus will be on the dashboard and the inbox screens (see attached) along with the common UI elements (Buttons, menu, fonts, forms...)
We want a simple and distinctive design

Target Market(s)

Worldwide

Industry/Entity Type

It Service

Number of Pages Required

3 page

Font styles to use
Sans Serif

Requirements
Must have
• New Onboarding page: this is a new page that is shown to user the first time they login to the platform. This will replace the current onboarding screen (setup SMS, Setup widget...etc)
• Dashboard page: to access important information and activate services (see screenshot from current site)
• Inbox page: to manage all the interactions with customers. (see screenshot from current site)
• UI elements (buttons, menus, forms, tables, fonts, color palette)

```html
<!DOCTYPE html>
<html lang="en">
<head>
<meta charset="utf-8">
<title>Velorant – Dashboard</title>
<link href="https://fonts.googleapis.com/css2?family=Open+Sans:wght@400;600;700&display=swap" rel="stylesheet">
<style>
:root{
  --sidebar:#3b3b3b;
  --accent:#f1582a;
  --bg:#ededed;
  --white:#fff;
  --line:#d8d8d8;
  --text:#333;
  --muted:#666;
  --panel-head:#a8a8a8;
  --green:#1cb51c;
  --blue:#1f78f0;
  --yellow:#f6b21b;
  --sky:#5bc0ec;
  --btn-blue:#3d9ff0;
}
*{box-sizing:border-box;margin:0;padding:0}
html,body{width:1200px;height:920px;overflow:hidden}
body{font-family:"Open Sans",sans-serif;background:var(--bg);color:var(--text);position:relative}
.sidebar{position:absolute;left:0;top:0;width:190px;height:920px;background:var(--sidebar);color:#fff}
.brand{display:flex;align-items:center;gap:7px;padding:20px 0 0 30px;font-size:22px;font-weight:700}
.brand-dot{width:20px;height:20px;border-radius:50%;background:#fff}
.nav{list-style:none;margin-top:40px}
.nav li{display:flex;align-items:center;height:39px;margin-bottom:25px;padding-left:35px;font-size:15px;font-weight:600}
.nav li.active{background:var(--accent)}
.nav svg{width:20px;height:20px;margin-right:23px;fill:#fff}
.feedback{position:absolute;left:15px;top:858px;display:flex;align-items:center;gap:13px;font-size:18px;font-weight:600}
.feedback svg{width:19px;height:15px;fill:#fff}
.topbar{position:absolute;left:190px;top:0;right:0;height:65px;background:var(--white);border-bottom:1px solid var(--line);display:flex;align-items:center;justify-content:flex-end;padding-right:52px}
.top-icon{position:relative;width:22px;height:22px;margin-right:22px}
.top-icon svg{width:22px;height:22px;fill:#888}
.badge{position:absolute;top:-6px;right:-6px;background:#e0262a;color:#fff;font-size:9px;width:13px;height:13px;border-radius:50%;text-align:center;line-height:13px}
.status{display:flex;align-items:center;gap:8px;font-size:13px;color:#444;margin:0 28px 0 8px}
.status i{width:10px;height:10px;border-radius:50%;background:#2ec53a}
.avatar{width:50px;height:50px;border-radius:50%;background:radial-gradient(circle at 50% 40%,#c99473,#5a4a3c);border:3px solid #eee}
.user{font-size:13px;color:#444;margin:0 44px 0 10px}
.help{width:19px;height:19px;border-radius:50%;background:#888;color:#fff;font-size:13px;font-weight:700;text-align:center;line-height:19px}
.page-title{position:absolute;left:213px;top:93px;font-size:22px;font-weight:600}
.date{position:absolute;left:889px;top:93px;width:258px;height:27px;border:1px solid #ccc;background:#f3f3f3;font-size:12px;display:flex;align-items:center;padding-left:12px;gap:7px;color:#444}
.date b{width:10px;height:10px;border:2px solid var(--accent);border-radius:2px}
.rule{position:absolute;left:213px;top:141px;width:934px;height:1px;background:var(--line)}
.stat{position:absolute;top:180px;width:220px;height:106px;background:var(--white);border:1px solid var(--line);display:flex;align-items:center;padding-left:14px}
.stat-ring{width:66px;height:66px;border-radius:50%;border:1px solid;display:flex;align-items:center;justify-content:center;margin-right:25px}
.stat-ring svg{width:28px;height:28px}
.stat-num{font-size:29px;color:#444;line-height:1.1}
.stat-label{font-size:14px;color:#666;margin-top:4px}
.panel{position:absolute;top:331px;height:500px;width:459px;background:var(--white);border:1px solid var(--line)}
.panel-head{height:41px;background:var(--panel-head);color:#fff;font-size:21px;font-weight:600;display:flex;align-items:center;gap:12px;padding-left:17px}
.panel-head svg{width:22px;height:20px;fill:#fff}
.chart-title{position:absolute;left:15px;top:64px;font-size:14px;font-weight:600}
.chart-sub{position:absolute;left:15px;top:90px;font-size:12px}
.chart-tools{position:absolute;right:21px;top:69px;display:flex;gap:7px}
.chart-tools span{width:35px;height:28px;border:1px solid #ccc;display:flex;align-items:center;justify-content:center}
.chart-tools span:first-child{background:#ddd;border-color:#ddd}
.chart{position:absolute;left:8px;top:130px}
.plan-title{position:absolute;left:15px;top:64px;font-size:15px;font-weight:600}
.plan-title span{font-weight:400;font-size:14px}
.btn{color:#fff;font-size:13px;display:flex;align-items:center;justify-content:center;gap:5px}
.btn svg{width:11px;height:11px;fill:#fff}
.upgrade{position:absolute;right:13px;top:62px;width:75px;height:24px;background:var(--green)}
.limits{position:absolute;left:19px;top:105px;display:flex;gap:17px}
.limit{position:relative;width:130px;height:60px;border:1px solid #ddd;box-shadow:0 1px 2px rgba(0,0,0,.08);display:flex;align-items:center;padding-left:9px;gap:9px;font-size:13px;color:#666;line-height:1.3}
.limit .ico{width:38px;height:38px;border-radius:50%;border:1px solid;display:flex;align-items:center;justify-content:center;flex:none}
.limit .ico svg{width:18px;height:18px}
.limit .count{position:absolute;top:-6px;right:-5px;background:#eee;border:1px solid #ccc;border-radius:8px;font-size:9px;padding:0 4px;color:#555}
.addon{position:absolute;left:18px;width:428px;border:1px solid #ccc;padding:0 22px;display:flex;justify-content:space-between;align-items:center}
.addon h3{font-size:14px;font-weight:600;color:#444;margin-bottom:2px}
.addon p{font-size:10.5px;line-height:1.7;color:#444}
.addon .btn{width:96px;height:27px;background:var(--btn-blue);flex:none}
.addon .btn.orange{background:var(--accent)}
.footer{position:absolute;left:494px;top:872px;font-size:12.5px;color:#555}
</style>
</head>
<body>
<aside class="sidebar">
  <div class="brand"><span class="brand-dot"></span>velorant</div>
  <ul class="nav">
    <li class="active"><svg viewBox="0 0 20 20"><path d="M10 2 1 10h3v8h5v-5h2v5h5v-8h3z"/></svg>Dashboard</li>
    <li><svg viewBox="0 0 20 20"><path d="M3 4h14l2 7v5H1v-5zm2 2-1 5h4l1 2h2l1-2h4l-1-5z"/></svg>Inbox</li>
    <li><svg viewBox="0 0 20 20"><path d="M12 1 19 8 8 19 1 12zm0 4-7 7 3 3 7-7z"/></svg>Tickets</li>
    <li><svg viewBox="0 0 20 20"><circle cx="10" cy="6" r="3"/><circle cx="4" cy="7" r="2.5"/><circle cx="16" cy="7" r="2.5"/><path d="M5 17c0-4 2-6 5-6s5 2 5 6zM0 15c0-3 1-5 4-5l1 1c-1 1-1 2-1 4zM20 15c0-3-1-5-4-5l-1 1c1 1 1 2 1 4z"/></svg>Clients</li>
    <li><svg viewBox="0 0 20 20"><path d="M1 2h2v15h16v2H1zM5 10h2v5H5zm4-4h2v9H9zm4 3h2v6h-2zm4-5h2v11h-2z"/></svg>Reports</li>
    <li><svg viewBox="0 0 20 20"><circle cx="7" cy="11" r="5"/><circle cx="15.5" cy="5" r="3"/><circle cx="15.5" cy="15" r="2.5"/></svg>Settings</li>
  </ul>
  <div class="feedback"><svg viewBox="0 0 19 15"><path d="M0 0h19v2L9.5 8 0 2zm0 4 9.5 6L19 4v11H0z"/></svg>Send Feedback</div>
</aside>

<header class="topbar">
  <div class="top-icon"><svg viewBox="0 0 22 22"><path d="M3 6h16l2 7v6H1v-6zm2 2-1 5h5l1 2h2l1-2h5l-1-5z"/></svg><span class="badge">4</span></div>
  <div class="top-icon"><svg viewBox="0 0 22 22"><path d="M13 1l8 8L9 21 1 13zm0 4-8 8 4 4 8-8z"/></svg></div>
  <div class="status"><i></i>Available ⌄</div>
  <div class="avatar" role="img" aria-label="Agent profile photo"></div>
  <div class="user">Rami Odell</div>
  <div class="help">?</div>
</header>

<h1 class="page-title">Dashboard</h1>
<div class="date"><b></b>23 December 2016-07 January 2017 ⌄</div>
<div class="rule"></div>

<div class="stat" style="left:213px">
  <div class="stat-ring" style="border-color:var(--green);background:#eaf8ea"><svg viewBox="0 0 28 28" fill="#1cb51c"><circle cx="14" cy="9" r="6"/><path d="M3 26c0-7 5-10 11-10s11 3 11 10z"/></svg></div>
  <div><div class="stat-num">0/0</div><div class="stat-label">Total Clients</div></div>
</div>
<div class="stat" style="left:451px">
  <div class="stat-ring" style="border-color:var(--blue);background:#e8f1fd"><svg viewBox="0 0 28 28" fill="#1f78f0"><path d="M18 2l8 8L10 26 2 18zm0 5L7 18l3 3 11-11z"/></svg></div>
  <div><div class="stat-num">0/0</div><div class="stat-label">Client Tickets</div></div>
</div>
<div class="stat" style="left:690px">
  <div class="stat-ring" style="border-color:var(--yellow);background:#fef6e4"><svg viewBox="0 0 28 28" fill="none" stroke="#f6b21b" stroke-width="2.5"><ellipse cx="12" cy="11" rx="9" ry="6"/><path d="M19 16c4 0 6 2 6 4l1 4-4-2"/></svg></div>
  <div><div class="stat-num">0</div><div class="stat-label">Total Chat</div></div>
</div>
<div class="stat" style="left:929px">
  <div class="stat-ring" style="border-color:var(--sky);background:#eaf6fc"><svg viewBox="0 0 28 28" fill="#5bc0ec"><path d="M2 6h24v3L14 16 2 9zm0 6 12 7 12-7v10H2z"/></svg></div>
  <div><div class="stat-num">0</div><div class="stat-label">Total SMS</div></div>
</div>

<section class="panel" style="left:213px">
  <div class="panel-head"><svg viewBox="0 0 22 20"><path d="M0 0h2v18h20v2H0zM5 9h2v7H5zm4-5h2v12H9zm4 3h2v9h-2zm4-4h2v13h-2z"/></svg>Reports</div>
  <div class="chart-title">Client total: Served vs non-served (Account)</div>
  <div class="chart-sub">from 23 December 2016 to 07 January 2017</div>
  <div class="chart-tools">
    <span><svg width="16" height="13" viewBox="0 0 16 13" fill="#f1582a"><path d="M0 12h16v1H0zM1 5h2v7H1zm4-3h2v10H5zm4 4h2v6H9zm4-5h2v11h-2z"/></svg></span>
    <span><svg width="18" height="12" viewBox="0 0 18 12" fill="none" stroke="#777" stroke-width="1.4"><path d="M1 0v11h17M2 9l5-5 3 3 6-6"/></svg></span>
  </div>
  <svg class="chart" width="440" height="280" viewBox="0 0 440 280" font-family="Open Sans, sans-serif">
    <g stroke="#ddd"><line x1="25" y1="19" x2="413" y2="19"/><line x1="25" y1="54" x2="413" y2="54"/><line x1="25" y1="88" x2="413" y2="88"/><line x1="25" y1="123" x2="413" y2="123"/><line x1="25" y1="157" x2="413" y2="157"/><line x1="25" y1="192" x2="413" y2="192"/></g>
    <g font-size="12" fill="#666"><text x="2" y="24">5</text><text x="2" y="59">4</text><text x="2" y="93">3</text><text x="2" y="128">2</text><text x="2" y="162">1</text><text x="2" y="197">0</text></g>
    <g font-size="9" fill="#555" text-anchor="middle"><text x="46" y="219">24. Dec</text><text x="98" y="219">26. Dec</text><text x="150" y="219">28. Dec</text><text x="202" y="219">30. Dec</text><text x="249" y="219">1. Jan</text><text x="292" y="219">2. Jan</text><text x="335" y="219">3. Jan</text><text x="379" y="219">4. Jan</text></g>
    <rect x="130" y="247" width="12" height="12" fill="#7cb5ec"/><text x="147" y="258" font-size="12" fill="#333">Served</text>
    <rect x="200" y="247" width="12" height="12" fill="#434348"/><text x="217" y="258" font-size="12" fill="#333">Non-Served</text>
    <rect x="417" y="5" width="20" height="20" fill="#1cb51c"/><circle cx="427" cy="12" r="3" fill="#fff"/><path d="M422 20c0-3 2-4 5-4s5 1 5 4z" fill="#fff"/>
    <rect x="417" y="35" width="20" height="20" fill="#1f78f0"/><path d="M429 40l4 4-6 6-4-4z" fill="#fff"/>
    <rect x="417" y="65" width="20" height="20" fill="#f6b21b"/><ellipse cx="427" cy="75" rx="5" ry="3.5" fill="#fff"/>
    <rect x="417" y="95" width="20" height="20" fill="#5bc0ec"/><ellipse cx="427" cy="105" rx="5" ry="3.5" fill="#fff"/>
  </svg>
</section>

<section class="panel" style="left:690px">
  <div class="panel-head"><svg viewBox="0 0 22 20"><path d="M2 5h6V2a2 2 0 0 1 4 0v3h5v5h3a2 2 0 0 1 0 4h-3v6H2v-5h2a2 2 0 0 0 0-4H2z"/></svg>Plan &amp; Add-ons</div>
  <div class="plan-title">Plan <span>(pro)</span></div>
  <div class="btn upgrade"><svg viewBox="0 0 12 12"><path d="M1 6l3 3 7-7 1 1-8 8-4-4z"/></svg>Upgrade</div>
  <div class="limits">
    <div class="limit"><span class="count">1/1</span><div class="ico" style="border-color:var(--yellow);background:#fef6e4"><svg viewBox="0 0 18 18" fill="#f6b21b"><circle cx="9" cy="5" r="3"/><circle cx="3.5" cy="6" r="2"/><circle cx="14.5" cy="6" r="2"/><path d="M3 16c0-4 2-6 6-6s6 2 6 6zM0 13c0-2 1-4 3-4v4zM18 13c0-2-1-4-3-4v4z"/></svg></div><div>Agents<br>Unlimited</div></div>
    <div class="limit"><span class="count">1</span><div class="ico" style="border-color:var(--blue);background:#e8f1fd"><svg viewBox="0 0 18 18" fill="#1f78f0"><path d="M6 2h6v3h5v11H1V5h5zm1 1v2h4V3z"/></svg></div><div>Departments<br>Unlimited</div></div>
    <div class="limit"><span class="count">1</span><div class="ico" style="border-color:var(--green);background:#eaf8ea"><svg viewBox="0 0 18 18" fill="#1cb51c"><path d="M4 1l3 4-2 2c1 3 3 5 6 6l2-2 4 3-2 3C8 17 1 10 1 4z"/></svg></div><div>Phones<br>Unlimited</div></div>
  </div>
  <div class="addon" style="top:190px;height:77px"><div><h3>Phone + SMS</h3><p>Allow clients to send SMS messages right to your inbox.<br>You may reply them with SMS message too.</p></div><div class="btn orange"><svg viewBox="0 0 12 12"><path d="M1 6l3 3 7-7 1 1-8 8-4-4z"/></svg>Add Phones</div></div>
  <div class="addon" style="top:279px;height:62px"><div><h3>Paynest</h3><p>Reseive one time payments with paynest</p></div><div class="btn"><svg viewBox="0 0 12 12"><path d="M1 6l3 3 7-7 1 1-8 8-4-4z"/></svg>Activate</div></div>
  <div class="addon" style="top:353px;height:62px"><div><h3>Chatwire</h3><p>Reseive chat messages ith Chatwire.</p></div><div class="btn"><svg viewBox="0 0 12 12"><path d="M1 6l3 3 7-7 1 1-8 8-4-4z"/></svg>Activate</div></div>
  <div class="addon" style="top:428px;height:62px"><div><h3>Beacon Messenger</h3><p>Reseive Chat messages with Beacon Messenger.</p></div><div class="btn"><svg viewBox="0 0 12 12"><path d="M1 6l3 3 7-7 1 1-8 8-4-4z"/></svg>Activate</div></div>
</section>

<footer class="footer">Copyright 2017, Velorant All rights reserved | Terms &amp; Conditions</footer>
</body>
</html>
```